Business Cards for new orthopaedic surgery practice

My husband and I are starting our own orthopaedic surgery practice. We are looking for a business card that is uniform, but one will have my name/title and the other will have his. You can just create one design with my name on it for now. But when I choose your design as the winning design I will ask that you add another copy with his name/title.

We are looking for classy, simple, elite all in one. We like dark blues/a little gold/yellow. Something that goes with our logo. We want our logo incorporated. Here is all the info you need:
Business name: RV Bone & Vitality Center
Location: 38517 North Willowmere Ave
Cedar Hollow, FL 33418
Phone: 954-218-4063
Fax: 954-582-7341
Email: info@myrvbonecare.example

Names: Lydia Vance, M.D.
Board Certified Hand and Upper Extremity Surgeon

Ebo Dansu, M.D.
Board Certified Hip & Knee Replacement/General Orthopaedic Surgeon

Can decide what you want to put on the back. Maybe a slogan:
Grounded in Care. Centered on You

I am just going to upload our logo. The only thing is if we select you as the winning design, the location, and phone numbers may change. We will need your help to update that once fully solidified.

Industry/Entity Type

Medical

Contact Information for Business Card

Colors
0054AA
0677BA
7BADD7
CADEEF
E8F1F8
0094D4
00A9DD
6FCCEA
C7EBF8
E9F6FB

Requirements
Must have
• class, appeal,
Should not have
• We want to air on the side of masculine if we are looking at masculine vs. feminine feel. But we still want it classy, sophisticated, and something we will love

```html
<!DOCTYPE html>
<html lang="en">
<head>
<meta charset="utf-8">
<title>RV Bone &amp; Vitality Center — Business Card</title>
<link rel="stylesheet" href="https://fonts.googleapis.com/css2?family=Cinzel:wght@700&family=Montserrat:wght@400;500;600&display=swap">
<style>
  :root {
    --page-bg: #e2e2e2;
    --navy: #2c3e84;
    --paper: #ffffff;
    --ink: #454545;
    --title-ink: #5b63a6;
    --soft-white: #ffffff;
    --muted-white: #b9bfdc;
  }
  * { box-sizing: border-box; margin: 0; padding: 0; }
  html, body {
    width: 1200px; height: 1200px; overflow: hidden;
    background: var(--page-bg);
  }
  .canvas { position: relative; width: 1200px; height: 1200px; }
  .card { position: absolute; left: 179px; width: 861px; height: 496px; }

  /* Front */
  .card-front { top: 84px; background: var(--navy); color: var(--soft-white); text-align: center; }
  .front-mark {
    position: absolute; left: 50%; top: 140px; transform: translateX(-50%);
    width: 90px; height: 90px; border-radius: 50%; background: var(--soft-white);
  }
  .front-name {
    position: absolute; left: 0; right: 0; top: 248px;
    font-family: "Cinzel", serif; font-weight: 700; font-size: 40px; line-height: 1;
    color: var(--soft-white);
  }
  .front-sub {
    position: absolute; left: 0; right: 0; top: 295px;
    display: flex; align-items: center; justify-content: center; gap: 14px;
    font-family: "Cinzel", serif; font-weight: 700; font-size: 30px; line-height: 1;
    letter-spacing: 1px;
  }
  .front-sub::before, .front-sub::after {
    content: ""; width: 86px; height: 2px; background: var(--soft-white);
  }
  .tagline {
    position: absolute; left: 0; right: 0; top: 336px;
    font-family: "Montserrat", sans-serif; font-weight: 400; font-size: 29px;
    letter-spacing: 0.3px;
  }
  .front-address {
    position: absolute; left: 0; right: 0; top: 451px;
    font-family: "Montserrat", sans-serif; font-size: 24px; color: var(--muted-white);
  }

  /* Back */
  .card-back { top: 622px; background: var(--paper); }
  .back-band { position: absolute; left: 0; right: 0; bottom: 0; height: 12px; background: var(--navy); }
  .rule { position: absolute; left: 229px; width: 5px; background: var(--navy); }
  .rule-brand { top: 72px; height: 111px; }
  .rule-person { top: 224px; height: 87px; }
  .rule-contact { top: 353px; height: 106px; }
  .back-mark {
    position: absolute; left: 60px; top: 38px;
    width: 130px; height: 130px; border-radius: 50%; background: var(--navy);
  }
  .back-name {
    position: absolute; left: 249px; top: 80px;
    font-family: "Cinzel", serif; font-weight: 700; font-size: 30px; line-height: 31px;
    color: var(--navy);
  }
  .person { position: absolute; left: 249px; top: 218px; font-family: "Montserrat", sans-serif; }
  .person-name { font-weight: 600; font-size: 35px; color: var(--ink); line-height: 1.15; }
  .person-title { font-weight: 500; font-size: 24px; color: var(--title-ink); line-height: 31px; }
  .contact-list {
    position: absolute; left: 249px; top: 345px; list-style: none;
    font-family: "Montserrat", sans-serif; font-size: 28px; color: var(--ink); letter-spacing: 0.6px;
  }
  .contact-item { display: flex; align-items: center; height: 41px; }
  .contact-icon { width: 26px; height: 26px; margin-right: 14px; fill: var(--navy); flex: none; }
</style>
</head>
<body>
<main class="canvas">
  <section class="card card-front" aria-label="Card front">
    <div class="front-mark"></div>
    <h1 class="front-name">RV BONE &amp; VITALITY</h1>
    <p class="front-sub">CENTER</p>
    <p class="tagline">Grounded in Care. Centered on You</p>
    <p class="front-address">38517 North Willowmere Ave Cedar Hollow, FL 33418</p>
  </section>

  <section class="card card-back" aria-label="Card back">
    <div class="back-mark"></div>
    <span class="rule rule-brand"></span>
    <p class="back-name">RV BONE &amp;<br>VITALITY<br>CENTER</p>

    <span class="rule rule-person"></span>
    <div class="person">
      <p class="person-name">Lydia Vance, M.D.</p>
      <p class="person-title">Board Certified Hand and<br>Upper Extremity Surgeon</p>
    </div>

    <span class="rule rule-contact"></span>
    <ul class="contact-list">
      <li class="contact-item">
        <svg class="contact-icon" viewBox="0 0 24 24" aria-hidden="true"><path d="M6.6 10.8c1.4 2.8 3.8 5.1 6.6 6.6l2.2-2.2c.3-.3.7-.4 1-.2 1.1.4 2.3.6 3.6.6.6 0 1 .4 1 1V20c0 .6-.4 1-1 1C10.6 21 3 13.4 3 4c0-.6.4-1 1-1h3.5c.6 0 1 .4 1 1 0 1.3.2 2.5.6 3.6.1.3 0 .7-.2 1z"/></svg>
        954-218-4063
      </li>
      <li class="contact-item">
        <svg class="contact-icon" viewBox="0 0 24 24" aria-hidden="true"><path d="M6 2h12v5H6z M3 8h18a1 1 0 0 1 1 1v8h-4v-4H6v4H2V9a1 1 0 0 1 1-1z M7 14h10v8H7z"/></svg>
        954-582-7341
      </li>
      <li class="contact-item">
        <svg class="contact-icon" viewBox="0 0 24 24" aria-hidden="true"><path d="M2 5h20v14H2z" fill="none" stroke="#2c3e84" stroke-width="2"/><path d="M2 5l10 8 10-8" fill="none" stroke="#2c3e84" stroke-width="2"/></svg>
        info@myrvbonecare.example
      </li>
    </ul>
    <div class="back-band"></div>
  </section>
</main>
</body>
</html>
```